Tallowmere Air Business Card Design

Design new, 2 sides, business cards for a residential and light commercial heating, air conditioning contractor.

Target Market(s)

Homeowners, small businesses

Industry/Entity Type

Business

Contact Information for Business Card

Dominic Westerhall
Phone - 862-415-2736
Email
Address - PO box 518
Brightwater NJ 07912
Website - www.HarborBreezeLLC.example

Requirements
Must have
• logo, company colors, standard size with no die cut, so I can use nova stamp

```html
<!DOCTYPE html>
<html lang="en">
<head>
<meta charset="utf-8">
<title>Tallowmere Air Business Card</title>
<link rel="stylesheet" href="https://fonts.googleapis.com/css2?family=Roboto:wght@400;500&display=swap">
<style>
  :root {
    --backdrop: #e9e5e0;
    --frost: #dcdad8;
    --frost-light: #eeedec;
    --accent-orange: #d8662a;
    --panel-red: #6c1420;
    --panel-red-light: #7e1c2a;
    --text-light: #f3e9e6;
    --name-orange: #e07a35;
    --brand-red: #7a1a26;
  }
  * { margin: 0; padding: 0; box-sizing: border-box; }
  html, body {
    width: 1200px;
    height: 969px;
    overflow: hidden;
    background: var(--backdrop);
    font-family: "Roboto", Arial, sans-serif;
  }
  .card {
    position: absolute;
    left: 100px;
    top: 200px;
    width: 1000px;
    height: 568px;
    display: flex;
    box-shadow: 0 10px 30px rgba(0,0,0,0.18);
  }
  .card-front {
    position: relative;
    width: 565px;
    height: 100%;
    background: linear-gradient(160deg, var(--frost-light), var(--frost));
    display: flex;
    align-items: center;
    justify-content: center;
  }
  .accent-stripe {
    position: absolute;
    left: 4px;
    top: 0;
    width: 22px;
    height: 100%;
    background: var(--accent-orange);
  }
  .brand {
    display: flex;
    align-items: center;
    gap: 16px;
    margin-left: 20px;
    margin-top: -30px;
  }
  .brand-dot {
    width: 28px;
    height: 28px;
    border-radius: 50%;
    background: var(--accent-orange);
  }
  .brand-name {
    font-size: 50px;
    font-weight: 500;
    color: var(--brand-red);
    letter-spacing: 1px;
    white-space: nowrap;
  }
  .card-details {
    flex: 1;
    height: 100%;
    background: linear-gradient(135deg, var(--panel-red-light), var(--panel-red));
    color: var(--text-light);
    text-align: right;
    padding: 100px 42px 0 0;
  }
  .person-name {
    font-size: 31px;
    font-weight: 500;
    color: var(--name-orange);
    letter-spacing: 1px;
  }
  .person-title {
    font-size: 25px;
    margin-top: 4px;
    letter-spacing: 1px;
  }
  .address {
    margin-top: 52px;
    font-size: 23px;
    line-height: 34px;
  }
  .contact-list {
    list-style: none;
    margin-top: 30px;
    font-size: 23px;
    line-height: 32.5px;
  }
  .contact-list li {
    display: flex;
    justify-content: flex-end;
    align-items: center;
    gap: 12px;
    white-space: nowrap;
  }
  .contact-list svg {
    width: 20px;
    height: 20px;
    fill: var(--accent-orange);
  }
</style>
</head>
<body>
  <div class="card">
    <section class="card-front">
      <div class="accent-stripe"></div>
      <div class="brand">
        <span class="brand-dot"></span>
        <span class="brand-name">Tallowmere Air</span>
      </div>
    </section>
    <section class="card-details">
      <p class="person-name">DOMINIC WESTERHALL</p>
      <p class="person-title">PRESIDENT</p>
      <p class="address">PO box 518<br>Brightwater NJ 07912</p>
      <ul class="contact-list">
        <li>862 415 2736
          <svg viewBox="0 0 20 20" aria-hidden="true"><path d="M2 7c0-3 4-4 8-4s8 1 8 4l-1 2-4-1V6H7v2L3 9zM5 10h10l2 7H3z"/></svg>
        </li>
        <li>862 415 2790
          <svg viewBox="0 0 20 20" aria-hidden="true"><path d="M6 1h8a1 1 0 0 1 1 1v16a1 1 0 0 1-1 1H6a1 1 0 0 1-1-1V2a1 1 0 0 1 1-1zm1 2v12h6V3z"/></svg>
        </li>
        <li>862 415 2755
          <svg viewBox="0 0 20 20" aria-hidden="true"><path d="M5 2h10v5H5zM2 8h16v8h-3v-3H5v3H2zM6 14h8v4H6z"/></svg>
        </li>
        <li>dominic@tallowmere.example
          <svg viewBox="0 0 20 20" aria-hidden="true"><path d="M2 5h16v1l-8 5-8-5zm0 3 8 5 8-5v7H2z"/></svg>
        </li>
        <li>www.TallowmereAirLLC.example
          <svg viewBox="0 0 20 20" aria-hidden="true"><circle cx="10" cy="10" r="8"/></svg>
        </li>
      </ul>
    </section>
  </div>
</body>
</html>
```